VELORA Brisbane Tiling Service

My name is Milos Brendt i need a business card for a new company. We are wall and floor tilers based in Brisbane, our company is Velorix Brisbane Tiling Service.
We would like a logo from our website used on our cards. Our website is www.velorix.com.au

I would like my Chatterbook and Postwave accounts on my card.

Industry/Entity Type

Business

Colors
0692cd
3176b5
33a6d7
85cae6

```html
<!DOCTYPE html>
<html lang="en">
<head>
<meta charset="utf-8">
<title>Velorix Brisbane Tiling Service – Business Card</title>
<link rel="stylesheet" href="https://fonts.googleapis.com/css2?family=Lato:wght@400;700&display=swap">
<style>
  :root {
    --brand-blue: #0692cd;
    --brand-deep: #3176b5;
    --brand-mid: #33a6d7;
    --brand-light: #85cae6;
    --ink: #333333;
    --ink-soft: #555555;
    --card: #ffffff;
    --tile-a: #f4f4f4;
    --tile-b: #e6e6e6;
    --edge-grey: #8a8a8a;
    --stage: #3a3a3a;
  }
  * { box-sizing: border-box; margin: 0; padding: 0; }
  html, body { width: 1200px; height: 997px; overflow: hidden; }
  body {
    background: var(--stage);
    font-family: "Lato", Arial, sans-serif;
    position: relative;
  }
  .card {
    position: absolute;
    width: 560px;
    height: 320px;
    background: var(--card);
    overflow: hidden;
    box-shadow: 0 12px 30px rgba(0,0,0,.45);
  }
  .card--back { left: 90px; top: 150px; }
  .card--front { left: 560px; top: 520px; }

  .tile-field {
    position: absolute;
    inset: 0;
    background: radial-gradient(ellipse at 50% 45%, var(--tile-a) 0%, var(--tile-b) 100%);
  }
  .band { position: absolute; left: 0; bottom: 0; width: 100%; height: 60px; }

  .logo {
    position: absolute;
    display: flex;
    align-items: center;
    gap: 12px;
  }
  .logo__square {
    width: 70px; height: 70px;
    background: var(--brand-blue);
  }
  .logo__name {
    font-size: 50px;
    font-weight: 400;
    color: var(--brand-blue);
    line-height: 0.9;
    letter-spacing: -0.5px;
  }
  .logo__tagline {
    font-size: 20px;
    color: var(--ink);
    line-height: 1.1;
  }
  .card--back .logo { left: 90px; top: 100px; }
  .card--front .logo { left: 150px; top: 40px; }
  .card--front .logo__square { width: 60px; height: 60px; }
  .card--front .logo__name { font-size: 44px; }
  .card--front .logo__tagline { font-size: 18px; }

  .website {
    position: absolute;
    left: 0; right: 0; top: 212px;
    text-align: center;
    font-weight: 700;
    font-size: 15px;
    letter-spacing: 4px;
    color: var(--ink);
  }

  .holder {
    position: absolute;
    right: 50px; top: 142px;
    text-align: left;
  }
  .holder__name { font-size: 22px; font-weight: 700; color: var(--brand-deep); }
  .holder__phone { font-size: 20px; color: var(--ink); letter-spacing: 1px; }

  .icon-tab {
    position: absolute;
    left: 0; top: 180px;
    width: 42px; height: 122px;
    background: var(--brand-blue);
    border-radius: 0 10px 10px 0;
    display: flex; flex-direction: column;
    align-items: center; justify-content: space-around;
    padding: 6px 0;
  }
  .contact-list {
    position: absolute;
    left: 60px; top: 185px;
    list-style: none;
    font-size: 13.5px;
    color: var(--ink);
  }
  .contact-list li { height: 29px; line-height: 29px; }
</style>
</head>
<body>

<section class="card card--back" aria-label="Business card back">
  <div class="tile-field" role="img" aria-label="Soft grey checkered tile pattern"></div>
  <svg class="band" viewBox="0 0 560 60" preserveAspectRatio="none" aria-hidden="true">
    <path d="M330 60 Q345 38 370 38 L560 38 L560 60 Z" fill="var(--brand-blue)"/>
    <path d="M300 60 Q318 46 340 46 L370 46 Q345 48 330 60 Z" fill="var(--edge-grey)" opacity=".5"/>
  </svg>
  <div class="logo">
    <div class="logo__square"></div>
    <div>
      <div class="logo__name">velorix</div>
      <div class="logo__tagline">brisbane tiling service</div>
    </div>
  </div>
  <p class="website">www.velorix.com.au</p>
</section>

<section class="card card--front" aria-label="Business card front">
  <div class="tile-field" role="img" aria-label="Soft grey checkered tile pattern"></div>
  <svg class="band" viewBox="0 0 560 60" preserveAspectRatio="none" aria-hidden="true">
    <path d="M330 60 Q345 38 370 38 L560 38 L560 60 Z" fill="var(--brand-blue)"/>
    <path d="M300 60 Q318 46 340 46 L370 46 Q345 48 330 60 Z" fill="var(--edge-grey)" opacity=".5"/>
  </svg>
  <div class="logo">
    <div class="logo__square"></div>
    <div>
      <div class="logo__name">velorix</div>
      <div class="logo__tagline">brisbane tiling service</div>
    </div>
  </div>

  <div class="holder">
    <div class="holder__name">Milos Brendt</div>
    <div class="holder__phone">0400 518 362</div>
  </div>

  <div class="icon-tab" aria-hidden="true">
    <svg width="16" height="20" viewBox="0 0 16 20"><rect x="3" y="1" width="10" height="18" rx="2" fill="none" stroke="#fff" stroke-width="2"/></svg>
    <svg width="20" height="14" viewBox="0 0 20 14"><rect x="1" y="1" width="18" height="12" fill="#fff"/><path d="M1 1 L10 8 L19 1" fill="none" stroke="var(--brand-blue)" stroke-width="1.5"/></svg>
    <svg width="14" height="14" viewBox="0 0 14 14"><circle cx="7" cy="7" r="6" fill="#fff"/></svg>
    <svg width="14" height="14" viewBox="0 0 14 14"><circle cx="7" cy="7" r="6" fill="#fff"/></svg>
  </div>
  <ul class="contact-list">
    <li>07 3000 4127</li>
    <li>info@velorix.com.au</li>
    <li>Postwave/ InfoVelorix</li>
    <li>Chatterbook/Velorix Brisbane Tiling Service</li>
  </ul>
</section>

</body>
</html>
```